Bluefinch Painting needs a Website

We need a website built for a Painting company I own, we mainly do residential painting, but don't want to be limited to that.

Need to have estimate request form.
Need pic's of past projects

I like the look of the website for http://www.harbor-brushworks.com
& "Westlake Home inspections"

My logo that was designed here on ArtHatch on the front page

I would like one of the houses I downloaded as part of the background
of the front page.

Target Market(s)

Home owners

Industry/Entity Type

Painting

Number of Pages Required

1 page

Font styles to use
Serif

Requirements
Must have
• Estimate request form for home owners to fill out -
• Name:
• Phone Number:
• Address:
• E-mail:
• Painting project description:
• And my info to:
• My phone number: (555) 318-7046
• My web address bluefinchpainting.example
Nice to have
• My logo that was designed here on ArtHatch

```html
<!DOCTYPE html>
<html lang="en">
<head>
<meta charset="utf-8">
<title>Bluefinch Painting</title>
<link href="https://fonts.googleapis.com/css2?family=Crimson+Text:wght@400;600&family=Roboto+Slab:wght@400;500&family=Arimo:wght@400;700&display=swap" rel="stylesheet">
<style>
:root{
  --blue:#1b7ac3;
  --blue-dark:#145e98;
  --ink:#222;
  --text:#3a3a3a;
  --muted:#777;
  --footer:#1b1b1b;
  --line:#ccc;
  --black:#050505;
}
*{box-sizing:border-box;margin:0;padding:0}
html,body{width:930px;height:1200px;overflow:hidden;background:#fff}
body{position:relative;font-family:"Arimo",Arial,sans-serif;color:var(--text)}
.abs{position:absolute}

/* header */
.brand{left:124px;top:14px;display:flex;align-items:center;gap:10px}
.brand-mark{width:36px;height:36px;background:var(--blue)}
.brand-name{font-family:"Crimson Text",serif;font-size:29px;color:var(--ink);letter-spacing:1px;line-height:1}
.trailer-photo{left:503px;top:8px;width:151px;height:70px;background:linear-gradient(180deg,#e9eaec,#c9cdd2);border:1px solid #bbb}
.estimate-btn{left:680px;top:4px;width:117px;height:22px;background:var(--blue);color:#fff;font-size:13px;text-align:center;line-height:22px;font-weight:700}
.call{left:683px;top:40px;display:flex;gap:6px;align-items:center}
.call small{display:block;font-size:11px;color:var(--ink)}
.call strong{display:block;font-size:15px;font-weight:400;color:var(--ink)}

/* nav */
.nav{left:0;top:78px;width:930px;height:32px;background:var(--blue);display:flex;padding-left:125px}
.nav a{font-family:"Roboto Slab",serif;font-size:12px;color:#fff;text-decoration:none;line-height:32px;padding:0 15px;border-right:1px solid #4a9ad6}
.nav a.active{background:var(--black);color:#fff;padding:0 11px;font-weight:500}
.nav a:last-child{border-right:0}

/* hero */
.hero{left:0;top:110px;width:930px;height:271px;background:linear-gradient(180deg,#c6d3dc 0%,#a7a184 45%,#6b7e45 85%,#4c6a2e 100%)}
.hero-arrow{top:248px;width:26px;height:24px;background:rgba(40,40,40,.8)}
.tagline{left:0;top:381px;width:930px;height:35px;background:#1e1e1e;color:#fff;font-family:"Roboto Slab",serif;font-size:17px;text-align:center;line-height:35px}
.welcome{left:0;top:416px;width:930px;height:168px;background:linear-gradient(180deg,#7e7f80,#6b6c6d 60%,#5d5e5e)}
.welcome h1{position:absolute;left:0;width:930px;top:21px;text-align:center;font-family:"Crimson Text",serif;font-weight:400;font-size:17px;color:#fff}
.welcome p{position:absolute;left:135px;width:660px;top:68px;text-align:center;font-size:9.5px;line-height:17px;color:#fff}
.read-more{background:var(--black);color:#fff;font-size:10px;line-height:18px;padding:0 7px;display:inline-block}

/* content */
.col h2{font-family:"Crimson Text",serif;font-weight:400;font-size:18px;color:var(--ink)}
.col .photo{margin-top:11px;width:206px;height:131px;border:2px solid #ddd}
.col p{margin-top:8px;font-size:9.5px;line-height:14.5px;width:210px}
.col .read-more{margin-top:9px}
.inquiry h2{font-family:"Crimson Text",serif;font-weight:400;font-size:18px;color:var(--ink);border-bottom:1px dashed #bbb;padding-bottom:3px;width:202px}
.field{position:absolute;left:609px;width:199px;height:20px;border:1px solid #c8c8c8;border-radius:2px;font-size:8.5px;font-style:italic;color:#777;padding:4px 8px}
.submit{left:614px;top:819px;width:61px;height:18px;background:var(--black);color:#fff;font-size:10px;font-weight:700;text-align:center;line-height:18px}

/* gallery */
.divider{left:133px;top:864px;width:676px;height:2px;background:linear-gradient(90deg,transparent,#e0e0e0,transparent)}
.gallery-icon{left:137px;top:885px;width:40px;height:40px;border:1px solid #ddd;border-radius:50%}
.gallery-title{left:186px;top:894px;font-family:"Crimson Text",serif;font-size:18px;color:var(--ink)}
.g-arrow{top:898px;width:13px;height:13px}
.thumb{top:938px;width:120px;height:96px;border:1px solid #555;padding:3px;background:#fff}
.thumb .img{width:100%;height:100%;position:relative}
.thumb span{position:absolute;left:0;bottom:0;width:100%;background:rgba(0,0,0,.6);color:#fff;font-family:"Crimson Text",serif;font-size:12px;padding:1px 6px}

/* footer */
.footer{left:0;top:1042px;width:930px;height:132px;background:var(--footer);color:#eee}
.footer h3{font-size:9.5px;font-weight:700;color:#fff;border-bottom:1px dashed #666;padding-bottom:2px;display:inline-block}
.footer li{list-style:none;font-size:9px;line-height:15.5px}
.contact-row{display:flex;font-size:9px;line-height:13.5px;margin-bottom:5px}
.contact-row b{width:22px}
.time-row{display:flex;align-items:center;gap:6px;font-size:8.5px;margin-bottom:10px}
.foot-brand{font-family:"Crimson Text",serif;font-size:17px;color:#fff;display:flex;align-items:center;gap:6px}
.foot-brand i{width:14px;height:14px;background:#fff;display:block}
.cards{display:flex;gap:3px}
.cards div{width:20px;height:13px;border-radius:2px}
.copyright{left:0;top:1174px;width:930px;height:26px;background:var(--blue);color:#fff;font-size:9px;text-align:center;line-height:26px}
</style>
</head>
<body>

<header>
  <div class="abs brand"><div class="brand-mark"></div><div class="brand-name">BLUEFINCH PAINTING</div></div>
  <div class="abs trailer-photo" role="img" aria-label="Company trailer with painting services lettering"></div>
  <div class="abs estimate-btn">Free Estimates</div>
  <div class="abs call">
    <svg width="22" height="22" viewBox="0 0 22 22"><circle cx="11" cy="11" r="10" fill="none" stroke="#1b7ac3" stroke-width="1.5"/><path d="M8 6c-1 1-1 4 1 7s4 4 5 3l1-1-2-2-1 1c-1-.5-2-2-2.5-3l1-1-1.5-2z" fill="#1b7ac3"/></svg>
    <div><small>Call Us Today</small><strong>555-318-7046</strong></div>
  </div>
</header>

<nav class="abs nav">
  <a class="active">Home</a><a>About Us</a><a>Exterior</a><a>Interior</a><a>Residential</a><a>Commerical</a><a>Past Projects</a><a>Contact Us</a>
</nav>

<section class="abs hero" role="img" aria-label="Two-storey tan house with red flower beds and green lawn"></section>
<svg class="abs hero-arrow" style="left:5px" viewBox="0 0 26 24"><path d="M15 7l-5 5 5 5" stroke="#fff" stroke-width="2.5" fill="none"/></svg>
<svg class="abs hero-arrow" style="left:896px" viewBox="0 0 26 24"><path d="M11 7l5 5-5 5" stroke="#fff" stroke-width="2.5" fill="none"/></svg>
<div class="abs tagline">PROVIDING QUALITY WORK AT AFFORDABLE PRICES</div>

<section class="abs welcome" role="img" aria-label="Company trucks and trailers parked in front of a house, dimmed">
  <h1>Welcome to Bluefinch Painting</h1>
  <svg style="position:absolute;left:339px;top:45px" width="200" height="10"><line x1="0" y1="3" x2="200" y2="3" stroke="#fff"/><line x1="0" y1="6" x2="200" y2="6" stroke="#fff"/><path d="M96 1l8 8M104 1l-8 8" stroke="#fff"/></svg>
  <p>Lorem ipsum dolor sit amet, consectetuer adipiscing elit, sed diam nonummy nibh euismod  rent ut laoreet dolore magna aliquam erat volutpat. Ut wisi enim ad minim veniam, quis nostrud lore xererci tation ullamcorper suscipit lobortis nisl ut aliquip ex ea commodo consequat. Duis autem revel eum iriure dolor in hendrerit in vulputate velit esse molestie consequat.</p>
  <svg style="position:absolute;left:375px;top:133px" width="190" height="10"><line x1="0" y1="5" x2="48" y2="5" stroke="#fff"/><line x1="47" y1="2" x2="58" y2="2" stroke="#fff"/><line x1="47" y1="8" x2="58" y2="8" stroke="#fff"/><line x1="122" y1="2" x2="133" y2="2" stroke="#fff"/><line x1="122" y1="8" x2="133" y2="8" stroke="#fff"/><line x1="133" y1="5" x2="190" y2="5" stroke="#fff"/></svg>
  <span class="read-more" style="position:absolute;left:434px;top:130px">Read More</span>
</section>

<section class="abs col" style="left:133px;top:602px">
  <h2>Residential Painting</h2>
  <div class="photo" role="img" aria-label="Painter on a ladder working on a house exterior" style="background:linear-gradient(180deg,#4f6a3a,#8c8a74 60%,#3c3a30)"></div>
  <p>Sed ut perspiciatis unde omnis iste natus error sit voluptatem accusantium doloremque laudantium, totam rem aperiam.</p>
  <span class="read-more">Read More</span>
</section>
<section class="abs col" style="left:370px;top:602px">
  <h2>Commerical Painting</h2>
  <div class="photo" role="img" aria-label="Painter rolling white paint on an interior wall" style="background:linear-gradient(90deg,#d8d6d2,#f2f1ee 70%,#1a2a48 95%)"></div>
  <p>Sed ut perspiciatis unde omnis iste natus error sit voluptatem accusantium doloremque laudantium, totam rem aperiam.</p>
  <span class="read-more">Read More</span>
</section>

<section class="abs inquiry" style="left:608px;top:602px">
  <h2>Quick Inquiry</h2>
</section>
<div class="field" style="top:637px">Name</div>
<div class="field" style="top:665px">Email</div>
<div class="field" style="top:694px">Phone</div>
<div class="field" style="top:722px">Type of Work</div>
<div class="field" style="top:753px;height:59px">Message</div>
<div class="abs submit">Submit</div>

<div class="abs divider"></div>
<div class="abs gallery-icon"><svg width="40" height="40" viewBox="0 0 40 40"><rect x="12" y="13" width="15" height="14" rx="2" fill="#1b7ac3"/><rect x="15" y="10" width="14" height="13" rx="2" fill="none" stroke="#1b7ac3" stroke-width="1.5"/><circle cx="19" cy="20" r="2.5" fill="#fff"/></svg></div>
<div class="abs gallery-title">Our Work Gallery</div>
<svg class="abs g-arrow" style="left:771px" viewBox="0 0 13 13"><rect width="13" height="13" fill="#111"/><path d="M8 3L5 6.5 8 10" stroke="#fff" stroke-width="1.8" fill="none"/></svg>
<svg class="abs g-arrow" style="left:787px" viewBox="0 0 13 13"><rect width="13" height="13" fill="#1b7ac3"/><path d="M5 3l3 3.5L5 10" stroke="#fff" stroke-width="1.8" fill="none"/></svg>

<div class="abs thumb" style="left:139px"><div class="img" role="img" aria-label="House exterior with garden" style="background:linear-gradient(180deg,#5d8fc6,#6e6a5c 55%,#4f7436)"><span>Exterior Painting 1</span></div></div>
<div class="abs thumb" style="left:273px"><div class="img" role="img" aria-label="Painter on white house siding" style="background:linear-gradient(180deg,#2a62b8,#c8ccd4 50%,#9aa0aa)"><span>Exterior Painting 2</span></div></div>
<div class="abs thumb" style="left:407px"><div class="img" role="img" aria-label="Painter at work on a beige wall" style="background:linear-gradient(180deg,#d8c79a,#e9e2cf 60%,#b7a87c)"><span>Exterior Painting 3</span></div></div>
<div class="abs thumb" style="left:541px"><div class="img" role="img" aria-label="Stucco house with lawn" style="background:linear-gradient(180deg,#8fb6dc,#b9ab90 50%,#4b7a34)"><span>Exterior Painting 4</span></div></div>
<div class="abs thumb" style="left:674px"><div class="img" role="img" aria-label="Grey two-storey house" style="background:linear-gradient(180deg,#a8b4c0,#6c6a66 55%,#4a4a46)"><span>Exterior Painting 5</span></div></div>

<footer class="abs footer">
  <div class="abs" style="left:133px;top:14px">
    <h3>Quick Links</h3>
    <ul style="margin-top:7px"><li>• Home</li><li>• About Us</li><li>• Services</li><li>• Past Projects</li><li>• Contact Us</li></ul>
  </div>
  <div class="abs" style="left:290px;top:14px">
    <h3>Contact Information</h3>
    <div style="margin-top:8px">
      <div class="contact-row"><b>A:</b><div>Bluefinch Painting<br>Street Name City Name<br>State Zipcode</div></div>
      <div class="contact-row" style="margin-top:6px"><b>P:</b><div>555-318-7046</div></div>
      <div class="contact-row" style="margin-top:4px"><b>E:</b><div>inquiry@bluefinchpainting.example</div></div>
    </div>
  </div>
  <div class="abs" style="left:472px;top:14px">
    <h3>Work Times</h3>
    <div style="margin-top:9px">
      <div class="time-row"><svg width="11" height="11" viewBox="0 0 11 11"><rect x="1" y="3" width="9" height="7" fill="none" stroke="#ddd"/><path d="M2 3l3.5-2 3.5 2" stroke="#ddd" fill="none"/></svg>Our work timings are:</div>
      <div class="time-row"><svg width="11" height="11" viewBox="0 0 11 11"><circle cx="5.5" cy="5.5" r="4.5" fill="none" stroke="#ddd"/><path d="M5.5 3v2.5h2" stroke="#ddd" fill="none"/></svg>Monday - Friday. 8AM - 8PM</div>
      <div class="time-row"><svg width="11" height="11" viewBox="0 0 11 11"><circle cx="5.5" cy="5.5" r="4.5" fill="none" stroke="#ddd"/><path d="M5.5 3v2.5h2" stroke="#ddd" fill="none"/></svg>Saturday:9AM - 4PM</div>
      <div class="time-row"><svg width="11" height="11" viewBox="0 0 11 11"><circle cx="5.5" cy="5.5" r="4.5" fill="none" stroke="#ddd"/><path d="M3.5 7.5c1-1 3-1 4 0" stroke="#ddd" fill="none"/></svg>Sunday: closed</div>
    </div>
  </div>
  <div class="abs" style="left:660px;top:27px">
    <div class="foot-brand"><i></i>BLUEFINCH PAINTING</div>
    <div style="margin-top:14px;font-size:9.5px;text-align:center;width:130px">We Accept</div>
    <div class="cards" style="margin-top:6px;margin-left:12px">
      <div style="background:#2b5fb0"></div><div style="background:#e8e8e8"></div><div style="background:#1a3f9a"></div><div style="background:#3aa1d8"></div><div style="background:#d8342b"></div>
    </div>
  </div>
</footer>
<div class="abs copyright">Copyright ©2015, BluefinchPainting  All Rights Reserved</div>

</body>
</html>
```